Kestrel Motion LLC Sports Therapy and Soft Tissue Injury solutions

We are a company that specializes in Sports Therapy, Physical therapy, muscular rehab, nutrition plans, and personal training. Kestrel Motion travels around the country and world treating athletes and people in the workforce that have Soft Tissue injuries. We are legally partnered with VMR(Vantor Muscle Recovery/vantorrecovery.example) in treating endurance athletes ex. SteelRidge triathalon. We educate our patients on how to sustain a healthy lifestyle.We need a web design that has a Home page summarizing our services, a Physical therapy page, a Personal training and nutrition page. Our ultimate goal is to build relationships with fitness centers, training facilities, and companies that are implementing preventative health measures for their employees. We want to incorporate the VMR logo and Steelridge logo attached in the website but, we want to use our own name (Kestrel Motion LLC) as the main draw. We will provide literature for the website.

Target Market(s)

Grindlane training gyms, Fitness centers, Dance studios, Companies looking for Corporate Wellness programs

Industry/Entity Type

Health And Wellness

Number of Pages Required

4 page

Font styles to use
Sans Serif

Requirements
Must have
• Stock Photos of Athletes training. Examples of Endurance Athletes and Cross training. A mesh of as many sports and training methods as possible. We are a new company and don't have many photos. Easy accessibility to change and add text as the company grows. Vantor Muscle recovery logo incorporated in the back ground of the website. Always visible but does not take over the web page
Nice to have
• Sleek and cool, and masculine design. We want the website to stand out without focusing on one individual. We want to use the website to brand the company (Kestrel Motion LLC) with easy access to social media platforms

```html
<!DOCTYPE html>
<html lang="en">
<head>
<meta charset="utf-8">
<title>Kestrel Motion LLC</title>
<link rel="stylesheet" href="https://fonts.googleapis.com/css2?family=Open+Sans:wght@400;600;700;800&display=swap">
<style>
:root{
  --red:#e10b17;
  --ink:#111111;
  --text:#333333;
  --muted:#666666;
  --light:#f2f2f2;
  --line:#d6d6d6;
  --white:#ffffff;
}
*{box-sizing:border-box;margin:0;padding:0}
html,body{width:714px;height:1200px;overflow:hidden}
body{position:relative;background:var(--white);font-family:"Open Sans",Arial,sans-serif;color:var(--text)}
.abs{position:absolute}
.btn{position:absolute;background:var(--red);color:var(--white);font-size:8px;display:flex;align-items:center;justify-content:center;letter-spacing:.2px;border:1px solid #b3000a}
.btn b{font-weight:800;margin-left:2px}
.accent{position:absolute;height:2px;width:20px;background:var(--red)}

/* header */
.site-header{position:absolute;left:0;top:0;width:714px;height:44px;background:var(--white)}
.brand{position:absolute;left:79px;top:11px;font-size:16px;font-weight:700;color:var(--ink);letter-spacing:-.1px}
.main-nav{position:absolute;left:293px;top:18px;display:flex;gap:15px;font-size:7px;color:var(--ink)}
.main-nav .active{color:var(--red);position:relative}
.main-nav .active::after{content:"";position:absolute;left:50%;top:12px;width:3px;height:3px;margin-left:-1.5px;border-radius:50%;background:var(--red)}
.search-btn{position:absolute;left:593px;top:0;width:42px;height:44px;background:var(--red)}

/* hero */
.hero{position:absolute;left:0;top:44px;width:714px;height:280px;background:linear-gradient(90deg,#2a2a2d 0%,#1a1a1d 55%,#111113 100%)}
.hero-kicker{position:absolute;left:362px;top:90px;font-size:12px;color:#e8e8e8}
.hero-title{position:absolute;left:360px;top:105px;font-size:19px;font-weight:700;color:var(--white)}
.hero-arrows{position:absolute;left:364px;top:182px}

/* welcome */
.welcome{position:absolute;left:0;top:324px;width:714px;height:140px;background:var(--light)}
.welcome h1{position:absolute;left:0;width:714px;top:18px;text-align:center;font-size:18px;font-weight:700;color:var(--ink)}
.welcome p{position:absolute;left:118px;width:478px;top:57px;text-align:center;font-size:6.3px;line-height:12.5px;color:var(--text)}

/* features */
.features{position:absolute;left:0;top:464px;width:714px;height:218px;background:var(--white)}
.features h2{position:absolute;left:95px;top:25px;font-size:12px;line-height:12.5px;font-weight:700;color:var(--ink)}
.features .intro{position:absolute;left:95px;top:68px;width:110px;font-size:6.2px;line-height:12.3px;color:var(--ink)}
.service-card{position:absolute;top:22px;width:131px;height:176px}
.service-card h3{height:36px;display:flex;align-items:center;justify-content:center;font-size:11.5px;font-weight:700;background:#dedede;color:var(--ink)}
.service-card.featured h3{background:var(--ink);color:var(--white)}
.service-photo{height:140px;position:relative}

/* news */
.news{position:absolute;left:0;top:682px;width:714px;height:229px;background:linear-gradient(180deg,#ececec,#dcdcdc)}
.news h2{position:absolute;left:0;width:714px;top:26px;text-align:center;font-size:12px;font-weight:700;color:var(--ink)}
.date-box{position:absolute;left:108px;top:67px;width:47px;height:64px;background:var(--white);text-align:center;color:var(--red);font-weight:700}
.date-box .day{font-size:17px;line-height:20px;margin-top:7px}
.date-box .month{font-size:13px;line-height:16px}
.date-box .year{font-size:6px;line-height:10px}
.news-photo{position:absolute;left:155px;top:67px;width:179px;height:127px;background:linear-gradient(180deg,#d65062 0%,#a65560 55%,#5e5654 100%)}
.news-body{position:absolute;left:334px;top:67px;width:272px;height:127px;background:var(--white)}
.news-body h3{position:absolute;left:21px;top:26px;width:240px;font-size:12px;line-height:15.5px;font-weight:700;color:var(--ink)}
.news-body .author{position:absolute;left:21px;top:62px;font-size:6.5px;font-style:italic;color:var(--red);display:flex;align-items:center;gap:5px}
.news-body p{position:absolute;left:23px;top:76px;width:242px;font-size:5.9px;line-height:12px;color:var(--text)}

/* contact */
.contact{position:absolute;left:0;top:911px;width:714px;height:235px;background:#f5f5f5}
.contact h2{position:absolute;left:0;width:714px;top:22px;text-align:center;font-size:12px;font-weight:700;color:var(--ink)}
.info{position:absolute;font-size:7px;color:var(--text);display:flex;align-items:center}
.info svg{margin-right:9px}
.follow{position:absolute;left:142px;top:129px;font-size:8px;font-weight:600;color:var(--ink)}
.social{position:absolute;display:flex;align-items:center;font-size:7.5px;color:var(--text)}
.social i{width:14px;height:14px;margin-right:10px;display:block}
.partner-badge{position:absolute;left:142px;top:199px;width:64px;height:20px;border-radius:10px;background:#cfcfcf}
.partner-divider{position:absolute;left:220px;top:195px;width:1px;height:30px;background:#9a9a9a}
.partner-kicker{position:absolute;left:234px;top:198px;font-size:4.5px;font-weight:700;color:var(--ink)}
.partner-name{position:absolute;left:233px;top:204px;font-size:13px;font-weight:800;color:var(--ink);letter-spacing:-.2px}
.field{position:absolute;left:359px;width:197px;background:var(--white);border:1px solid var(--line);border-radius:2px;font-size:5.5px;color:var(--muted);padding:8px 9px}

/* footer */
.site-footer{position:absolute;left:0;top:1146px;width:714px;height:54px;background:var(--white);border-top:1px solid #e4e4e4}
.footer-nav{position:absolute;left:0;width:714px;top:18px;display:flex;justify-content:center;gap:15px;font-size:7px;color:var(--ink)}
.footer-nav .active{color:var(--red)}
.copyright{position:absolute;left:0;width:714px;top:37px;text-align:center;font-size:5.6px;color:var(--text)}
</style>
</head>
<body>

<header class="site-header">
  <div class="brand">Kestrel Motion LLC</div>
  <nav class="main-nav">
    <span class="active">Home</span><span>Services</span><span>Physical Therapy</span><span>Personal Training</span><span>Nutrition</span><span>Contact Us</span>
  </nav>
  <div class="search-btn">
    <svg width="42" height="44" viewBox="0 0 42 44"><circle cx="20" cy="20" r="5" fill="none" stroke="#fff" stroke-width="2"/><line x1="23.5" y1="23.5" x2="27" y2="27" stroke="#fff" stroke-width="2.4" stroke-linecap="round"/></svg>
  </div>
</header>

<section class="hero" role="img" aria-label="Hero photo: athlete running over a dark technical backdrop">
  <div class="hero-kicker">We are a company that</div>
  <div class="hero-title">Specializes in Sports Therapy.</div>
  <div class="btn" style="left:361px;top:143px;width:81px;height:22px;font-size:9px">LEARN <b>MORE</b></div>
  <svg class="hero-arrows" width="26" height="14" viewBox="0 0 26 14"><polyline points="6,2 1,7 6,12" fill="none" stroke="#fff" stroke-width="1.5"/><polyline points="18,2 23,7 18,12" fill="none" stroke="#fff" stroke-width="1.5"/></svg>
</section>

<section class="welcome">
  <div class="accent" style="left:347px;top:12px"></div>
  <h1>Welcome!</h1>
  <p>Kestrel Motion Mission statement-We are a company that specializes in Sports Therapy, Physical therapy, muscular rehab, nutrition plans, and personal training. Kestrel Motion travels around the country and world treating athletes and people in the workforce that have Soft tissue injuries. We educate our patients on how to sustain a healthy lifestyle!</p>
  <div class="btn" style="left:324px;top:108px;width:61px;height:17px">READ <b>MORE</b></div>
</section>

<section class="features">
  <div class="accent" style="left:95px;top:21px"></div>
  <h2>Feature our<br>services</h2>
  <svg class="abs" style="left:174px;top:27px" width="20" height="18" viewBox="0 0 20 18">
    <circle cx="7" cy="9" r="4.5" fill="none" stroke="#111" stroke-width="3" stroke-dasharray="2 1.5"/><circle cx="7" cy="9" r="1.6" fill="#111"/>
    <circle cx="15" cy="4" r="2.8" fill="none" stroke="#111" stroke-width="2" stroke-dasharray="1.4 1"/>
    <circle cx="15" cy="14" r="2.8" fill="none" stroke="#111" stroke-width="2" stroke-dasharray="1.4 1"/>
  </svg>
  <p class="intro">Nemo enim ipsam voluptatem quia voluptas sit aspernatur aut odit aut fugit, sed quia consequuntur magni dolores eos qui ratione voluptatem sequi nesciunt.</p>
  <div class="btn" style="left:95px;top:139px;width:61px;height:17px">READ <b>MORE</b></div>

  <div class="service-card featured" style="left:213px">
    <h3>Physical Therapy</h3>
    <div class="service-photo" role="img" aria-label="Photo: therapist treating a patient, red overlay" style="background:#e9585c">
      <svg class="abs" style="left:56px;top:60px" width="20" height="20" viewBox="0 0 20 20"><line x1="10" y1="1" x2="10" y2="19" stroke="#fff" stroke-width="1.3"/><line x1="1" y1="10" x2="19" y2="10" stroke="#fff" stroke-width="1.3"/></svg>
    </div>
  </div>
  <div class="service-card" style="left:351px">
    <h3>Personal Training</h3>
    <div class="service-photo" role="img" aria-label="Photo: athlete training with suspension straps in a gym" style="background:linear-gradient(180deg,#4a4a4a,#6a6a6a)"></div>
  </div>
  <div class="service-card" style="left:489px">
    <h3>Muscular rehab</h3>
    <div class="service-photo" role="img" aria-label="Photo: man holding a sore neck" style="background:linear-gradient(180deg,#d4d4d4,#b4b4b4)"></div>
  </div>
</section>

<section class="news">
  <div class="accent" style="left:347px;top:14px"></div>
  <h2>NEWS</h2>
  <div class="date-box"><div class="day">03</div><div class="month">JAN</div><div class="year">2017</div></div>
  <div class="news-photo" role="img" aria-label="Photo: athletes lifting barbells in a red-walled gym"></div>
  <div class="news-body">
    <h3>NOR AGAIN IS THERE ANYONE WHO LOVES OR PURSUES OR DESIRES...</h3>
    <div class="author">
      <svg width="7" height="8" viewBox="0 0 7 8"><rect x="1" y="3.5" width="5" height="4" fill="none" stroke="#e10b17" stroke-width=".9"/><path d="M2 3.5V2.3a1.5 1.5 0 0 1 3 0v1.2" fill="none" stroke="#e10b17" stroke-width=".9"/></svg>
      by Lorium ipsum
    </div>
    <p>Quis autem vel eum iure reprehenderit qui in ea voluptate velit esse quam nihil molestiae consequatur, vel illum qui dolorem eum fugiat quo voluptas nulla pariatur...</p>
  </div>
</section>

<section class="contact">
  <h2>CONTACT US</h2>
  <div class="info" style="left:146px;top:64px">
    <svg width="8" height="8" viewBox="0 0 8 8"><path d="M1.5 .5l1.6 1.6-.9 1.1c.6 1.1 1.4 1.9 2.5 2.5l1.1-.9 1.6 1.6-1 1.1C3.5 7.4.6 4.5.4 1.5z" fill="#333"/></svg>
    Phone :&nbsp; (555)214-0738
  </div>
  <div class="info" style="left:146px;top:87px;align-items:flex-start">
    <svg width="6" height="9" viewBox="0 0 6 9" style="margin-top:1px"><path d="M3 0a3 3 0 0 1 3 3c0 2-3 6-3 6S0 5 0 3a3 3 0 0 1 3-3z" fill="#333"/><circle cx="3" cy="3" r="1" fill="#f5f5f5"/></svg>
    <span style="line-height:17px;margin-top:-4px">Address : 418 Larkspur Ave Suite 210<br>Fernvale, California, 90412</span>
  </div>
  <div class="follow">Follow Us</div>
  <div class="social" style="left:142px;top:151px"><i style="background:#1f4c8f"></i>Friendwall</div>
  <div class="social" style="left:212px;top:153px"><i style="background:#1ca6e0"></i>Chirpline</div>
  <div class="social" style="left:142px;top:172px"><i style="background:#d21c22"></i>Clipstream</div>
  <div class="social" style="left:212px;top:172px"><i style="background:#e33b2b"></i>Circlenet</div>
  <div class="partner-badge" role="img" aria-label="Partner badge"></div>
  <div class="partner-divider"></div>
  <div class="partner-kicker">PROUD PARTNER</div>
  <div class="partner-name">STEELRIDGE</div>

  <div class="field" style="top:65px;height:18px;padding-top:5px">NAME</div>
  <div class="field" style="top:91px;height:18px;padding-top:5px">EMAIL</div>
  <div class="field" style="top:118px;height:43px;padding-top:6px">MESSAGE</div>
  <div class="btn" style="left:359px;top:167px;width:60px;height:17px;font-weight:700">SUBMIT</div>
</section>

<footer class="site-footer">
  <nav class="footer-nav">
    <span class="active">Home</span><span>Services</span><span>Physical Therapy</span><span>Personal Training</span><span>Nutrition</span><span>Contact Us</span>
  </nav>
  <div class="copyright">Copyrights © 2017, www.kestrelmotion.example. All Rights Reserved.</div>
</footer>

</body>
</html>
```